Sports Event - Web Design Project

We run an event called GRIT & GLORY which is "Ireland's Wildest 10K Ordeal" - so running through water, covered in mud, through electric fences etc. Similar type event to GrimSlogger or Vorlaxian Dash internationally

Have 2,500 people signed up for next event in January so want to revamp our current website www.gritandglory.ie and bring it up to the next level.

We are looking for 3 pages to be deisgned: a template site page, a Home Page & an Events Page with interactive map. I have already made a "home made" design of what we want - so this design will give you a good idea of the style and colours we want...then its up to you to add your skill and personality to make the new website exciting, stylish and professional.
Updates

I have just posted a web page which gives a bit more detail about the 3 pages we are looking for, the style etc

we have our own web developers who will take your design and implement it into the back end of our customised website...so whoever gets the job, I will get them to speak with our developer about what is the best way to give the final artwork etc to us. 

Here is the webpage with our "Homemade" designs on it to give you an idea of all the things we are looking for

http://www.brambleroute.ie/News/New-Website-Screenshots-post-35.htm

Here is the GRIT & GLORY logo - sorry dont know how else up to upload it

For the Interactive Map (Event Page), go to the following link for actual course:

Target Market(s)

Male and female, sporty and non-sporty (lots of people do this event for charity). Aged 21-45. People looking for a fun challenge

Industry/Entity Type

Events

Requirements
Must have
• Require 3 pages:
1. Home Page (with video being central point)
2. Events Page with interactive map
3. Template Site Page

See this link for more info:

We also require each of these designs to be enabled in the following formats:
1. PC / Desktop
2. iPad / Tablet
3. Phone

Must use the orange, red and black of GRIT & GLORY logo, as well as some type of hellish fire/flames

```html
<!DOCTYPE html>
<html lang="en">
<head>
<meta charset="utf-8">
<title>GRIT &amp; GLORY Winter – Home</title>
<link rel="stylesheet" href="https://fonts.googleapis.com/css2?family=Roboto+Condensed:wght@400;700&family=PT+Sans:wght@400;700&display=swap">
<style>
:root{
  --fire-deep:#b81e06;
  --fire-red:#d8340a;
  --fire-mid:#ef5a12;
  --fire-light:#f99a2a;
  --fire-glow:#fcc24a;
  --fire-white:#ffe08a;
  --nav-top:#f07a18;
  --nav-bottom:#d84a0c;
  --panel-dark:#333333;
  --black:#000000;
  --white:#ffffff;
  --cream:#fde6c8;
  --soft-text:#f6c79a;
  --join-yellow:#f2c20c;
  --charity-red:#c42a12;
  --btn-red:#7a1a0a;
  --footer:#171311;
}
*{box-sizing:border-box;margin:0;padding:0}
html,body{width:1200px;height:1194px;overflow:hidden}
body{position:relative;font-family:"PT Sans",sans-serif;color:var(--white);background:var(--fire-mid)}
.abs{position:absolute}
.heading{font-family:"Roboto Condensed",sans-serif;font-weight:700}

/* fiery backdrop: layered soft glows suggesting rising flame tongues */
.fire-backdrop{left:0;top:0;width:1200px;height:1194px;
  background:
    radial-gradient(ellipse 70px 260px at 640px 640px,rgba(255,224,138,.55) 0%,rgba(255,224,138,0) 100%),
    radial-gradient(ellipse 60px 220px at 470px 700px,rgba(255,224,138,.5) 0%,rgba(255,224,138,0) 100%),
    radial-gradient(ellipse 80px 240px at 300px 740px,rgba(252,194,74,.55) 0%,rgba(252,194,74,0) 100%),
    radial-gradient(ellipse 70px 200px at 820px 560px,rgba(255,224,138,.45) 0%,rgba(255,224,138,0) 100%),
    radial-gradient(ellipse 90px 260px at 1140px 700px,rgba(252,194,74,.5) 0%,rgba(252,194,74,0) 100%),
    radial-gradient(ellipse 60px 230px at 60px 820px,rgba(252,194,74,.5) 0%,rgba(252,194,74,0) 100%),
    radial-gradient(ellipse 60px 180px at 1150px 360px,rgba(255,200,90,.45) 0%,rgba(255,200,90,0) 100%),
    radial-gradient(ellipse 70px 200px at 40px 420px,rgba(255,170,60,.5) 0%,rgba(255,170,60,0) 100%),
    radial-gradient(ellipse 120px 90px at 700px 50px,rgba(255,170,60,.6) 0%,rgba(255,170,60,0) 100%),
    radial-gradient(ellipse 460px 260px at 520px 780px,rgba(252,194,74,.9) 0%,rgba(252,194,74,0) 100%),
    radial-gradient(ellipse 520px 340px at 1000px 120px,rgba(184,30,6,.9) 0%,rgba(184,30,6,0) 100%),
    radial-gradient(ellipse 300px 380px at 20px 260px,rgba(184,30,6,.85) 0%,rgba(184,30,6,0) 100%),
    radial-gradient(ellipse 260px 300px at 1180px 620px,rgba(200,40,8,.7) 0%,rgba(200,40,8,0) 100%),
    radial-gradient(ellipse 300px 200px at 100px 1000px,rgba(200,40,8,.7) 0%,rgba(200,40,8,0) 100%),
    linear-gradient(180deg,var(--fire-red) 0%,var(--fire-mid) 30%,var(--fire-light) 62%,var(--fire-mid) 82%,var(--fire-deep) 100%);}
.top-edge{left:0;top:0;width:1200px;height:6px;background:#e8a08a}

/* brand */
.brand{left:92px;top:40px;width:270px}
.brand-name{font-family:"Roboto Condensed",sans-serif;font-weight:700;font-size:30px;line-height:32px;color:var(--white)}
.brand-sub{font-family:"Roboto Condensed",sans-serif;font-weight:700;font-size:13px;color:var(--cream);margin-top:6px}

/* nav */
.main-nav{left:84px;top:139px;width:1024px;height:56px;border-radius:6px 6px 0 0;
  background:linear-gradient(180deg,var(--nav-top),var(--nav-bottom));display:flex}
.main-nav a{font-family:"Roboto Condensed",sans-serif;font-weight:700;font-size:16px;color:var(--white);
  text-decoration:none;display:flex;align-items:center;justify-content:center;border-right:1px solid rgba(120,30,0,.5);height:100%}

/* video */
.video-panel{left:84px;top:196px;width:672px;height:389px;background:var(--black);border-radius:8px;border:1px solid #5a2a10}
.video-bar{left:82px;top:7px;width:533px;height:33px;background:#1e1e1e;display:flex;align-items:center;padding-left:14px;
  font-family:"Roboto Condensed",sans-serif;font-size:20px;color:#e4e4e4}
.video-bar .actions{margin-left:auto;display:flex;font-size:14px;height:100%}
.video-bar .actions span{display:flex;align-items:center;padding:0 12px;border-left:1px solid #444}
.video-still{left:82px;top:40px;width:533px;height:329px;
  background:
    radial-gradient(ellipse 120px 160px at 80% 45%,rgba(140,130,150,.45) 0%,rgba(140,130,150,0) 100%),
    radial-gradient(ellipse 140px 120px at 40% 40%,rgba(120,110,140,.4) 0%,rgba(120,110,140,0) 100%),
    linear-gradient(180deg,#3e4a30 0%,#4a4a3c 45%,#5a5448 75%,#3a3630 100%);}
.play{left:302px;top:172px}

/* signup */
.signup{left:764px;top:196px;width:345px;height:169px;background:linear-gradient(180deg,#e8620e,#c9340c);border:2px solid #f2803a}
.signup h2{position:absolute;left:30px;top:20px;font-size:30px}
.signup p{position:absolute;left:30px;top:56px;width:290px;font-size:12.5px;line-height:23px;color:var(--cream)}
.signup-btn{left:27px;top:113px;width:201px;height:36px;background:var(--btn-red);display:flex;align-items:center;
  padding-left:30px;font-family:"Roboto Condensed",sans-serif;font-weight:700;font-size:15px}
.signup-btn svg{position:absolute;left:11px;top:12px}

/* newsletter */
.unite{left:764px;top:368px;width:345px;height:211px;background:var(--panel-dark);border:8px solid #262020}
.unite h2{position:absolute;left:20px;top:16px;font-family:"Roboto Condensed",sans-serif;font-weight:400;font-size:27px}
.unite p{position:absolute;left:22px;top:50px;width:240px;font-size:12.5px;line-height:20px;color:#c8c8c8}
.unite .field{left:17px;top:96px;width:208px;height:36px;background:#2a2a2a;border:1px solid #555}
.unite .join{left:225px;top:96px;width:79px;height:36px;background:var(--join-yellow);color:#c0340a;
  font-family:"Roboto Condensed",sans-serif;font-weight:700;font-size:20px;display:flex;align-items:center;justify-content:center}
.socials{left:22px;top:144px;display:flex;gap:8px}
.socials span{width:28px;height:28px;border-radius:3px}

/* events */
.section-title{font-size:25px;color:var(--white)}
.event-card{width:160px;top:654px}
.event-photo{width:155px;height:140px;background:var(--white);padding:6px}
.event-photo div{width:100%;height:100%}
.event-date{font-family:"Roboto Condensed",sans-serif;font-weight:700;font-size:15px;margin:10px 0 0 5px}
.event-text{font-size:11.5px;line-height:20px;color:var(--soft-text);margin:2px 0 0 5px}

/* charity */
.charity{left:787px;top:641px;width:295px;height:211px;background:linear-gradient(180deg,#fff,#ececec);border:3px solid #f3d9c8}
.charity h2{position:absolute;left:25px;top:20px;font-family:"Roboto Condensed",sans-serif;font-weight:400;font-size:26px;color:var(--charity-red)}
.charity p{position:absolute;left:25px;top:57px;width:140px;font-size:11px;line-height:18px;color:var(--charity-red)}
.charity .art{left:160px;top:65px;width:128px;height:120px;
  background:
    radial-gradient(ellipse 30px 30px at 58% 25%,rgba(90,140,60,.6) 0%,rgba(90,140,60,0) 100%),
    radial-gradient(ellipse 60px 22px at 55% 80%,#d4ad5a 0%,rgba(228,207,149,0) 100%);}
.charity .help{left:24px;top:143px;width:90px;height:35px;background:linear-gradient(180deg,#ec5a18,#c8300c);
  font-family:"Roboto Condensed",sans-serif;font-weight:700;font-size:14px;display:flex;align-items:center;justify-content:center}

/* partners */
.partners{left:84px;top:896px;width:989px;height:140px;background:var(--panel-dark)}
.partners h2{position:absolute;left:21px;top:16px;font-size:24px}
.partner-row{left:76px;top:50px;display:flex;gap:24px;align-items:center;height:50px}
.badge{background:#5e5e5e;border-radius:4px;height:30px}
.arrow{top:58px}

/* footer */
.footer-edge{left:0;top:1030px}
.footer{left:0;top:1068px;width:1200px;height:126px;background:linear-gradient(180deg,#2a1a10,var(--footer) 40%)}
.footer-nav{left:107px;top:28px;display:flex;font-family:"Roboto Condensed",sans-serif;font-weight:700;font-size:13px}
.footer-nav a{color:var(--white);text-decoration:none}
.footer-nav .sep{margin:0 13px;color:#cfcfcf}
.copyright{left:107px;top:59px;font-size:12px;color:#d8d8d8}
</style>
</head>
<body>

<div class="fire-backdrop abs" role="img" aria-label="Blazing flames backdrop in red, orange and yellow"></div>
<div class="top-edge abs"></div>

<header class="brand abs">
  <div class="brand-name">GRIT &amp; GLORY<br>WINTER</div>
  <div class="brand-sub">NEW DATE ADDED · Sun 3rd Feb 2013</div>
</header>

<nav class="main-nav abs">
  <a href="#" style="width:101px">HOME</a>
  <a href="#" style="width:101px">EVENTS</a>
  <a href="#" style="width:133px">GET INVOLVED</a>
  <a href="#" style="width:101px">PHOTOS</a>
  <a href="#" style="width:98px">VIDEOS</a>
  <a href="#" style="width:144px">HALL OF FRAME</a>
  <a href="#" style="width:130px">WHO WE ARE</a>
  <a href="#" style="width:130px;border-right:0">CONTACT US</a>
</nav>

<section class="video-panel abs">
  <div class="video-bar abs">Ireland's Wildest 10K Ordeal - HE
    <div class="actions"><span>Share</span><span>▼&nbsp; More info</span></div>
  </div>
  <div class="video-still abs" role="img" aria-label="Video still of muddy runners climbing through a forest trail"></div>
  <svg class="play abs" width="92" height="66" viewBox="0 0 92 66">
    <rect width="92" height="66" rx="16" fill="#111" opacity=".9"/>
    <path d="M36 18 L62 33 L36 48 Z" fill="#fff"/>
  </svg>
</section>

<section class="signup abs">
  <h2 class="heading">SIGN UP NOW</h2>
  <p>Proin dui lectus, cursus eu, mattis laoreet, viverra sit amet, quam. Curabitur vel dolor ultrices</p>
  <div class="signup-btn abs">
    <svg width="10" height="12" viewBox="0 0 10 12"><path d="M1 0 L9 6 L1 12 Z" fill="#e8620e"/></svg>
    CLICK HERE FOR SIGN UP
  </div>
</section>

<section class="unite abs">
  <h2>Devil Unite!</h2>
  <p>Etiam est nunc, venenatis in, tristique eu, imperdiet ac, nisl.</p>
  <div class="field abs"></div>
  <div class="join abs">Join</div>
  <div class="socials abs" aria-label="Social links">
    <span style="background:#3b5a9a"></span>
    <span style="background:#1a7bb0"></span>
    <span style="background:#e8631a"></span>
    <span style="background:#c8281c"></span>
  </div>
</section>

<h2 class="section-title heading abs" style="left:95px;top:612px">Upcoming Events</h2>

<article class="event-card abs" style="left:93px">
  <div class="event-photo"><div role="img" aria-label="Runners with race numbers at the start line" style="background:radial-gradient(ellipse at 50% 60%,#7a7f7a,#3e4a3a)"></div></div>
  <div class="event-date">3rd Feb 2013</div>
  <div class="event-text">Cum sociis natoque penatibus et magnis dis parturient</div>
</article>
<article class="event-card abs" style="left:264px">
  <div class="event-photo"><div role="img" aria-label="Mud-covered participants celebrating together" style="background:radial-gradient(ellipse at 50% 65%,#b8aa92,#55603a)"></div></div>
  <div class="event-date">10th Feb 2013</div>
  <div class="event-text">Cum sociis natoque penatibus et magnis dis parturient</div>
</article>
<article class="event-card abs" style="left:436px">
  <div class="event-photo"><div role="img" aria-label="Runners crossing a tyre obstacle" style="background:linear-gradient(180deg,#5e7a44 0%,#4a5a40 55%,#2e3430 100%)"></div></div>
  <div class="event-date">3rd Feb 2013</div>
  <div class="event-text">Cum sociis natoque penatibus et magnis dis parturient</div>
</article>
<article class="event-card abs" style="left:607px">
  <div class="event-photo"><div role="img" aria-label="Runners descending a grassy hill" style="background:linear-gradient(170deg,#3e4e34,#6a7e52 60%,#5a6e44)"></div></div>
  <div class="event-date">3rd Feb 2013</div>
  <div class="event-text">Cum sociis natoque penatibus et magnis dis parturient</div>
</article>

<section class="charity abs">
  <h2>My Charity</h2>
  <p>Praesent vitae lacus. Ut velit enim, vestibulum non, fermentum nec, h endrerit quis, leo.</p>
  <div class="art abs" role="img" aria-label="Seedling growing from a pile of coins"></div>
  <div class="help abs">Helping Now</div>
</section>

<section class="partners abs">
  <h2 class="heading">Our Partners</h2>
  <svg class="arrow abs" style="left:14px" width="22" height="34" viewBox="0 0 22 34"><path d="M18 2 L4 17 L18 32" stroke="#6a6a6a" stroke-width="6" fill="none"/></svg>
  <div class="partner-row abs" aria-label="Partner badges">
    <span class="badge" style="width:66px"></span>
    <span class="badge" style="width:52px"></span>
    <span class="badge" style="width:66px"></span>
    <span class="badge" style="width:96px"></span>
    <span class="badge" style="width:56px"></span>
    <span class="badge" style="width:58px;border-radius:50%;height:40px"></span>
    <span class="badge" style="width:78px"></span>
    <span class="badge" style="width:68px"></span>
    <span class="badge" style="width:44px;border-radius:50%;height:44px"></span>
  </div>
  <svg class="arrow abs" style="left:950px" width="22" height="34" viewBox="0 0 22 34"><path d="M4 2 L18 17 L4 32" stroke="#6a6a6a" stroke-width="6" fill="none"/></svg>
</section>

<svg class="footer-edge abs" width="1200" height="40" viewBox="0 0 1200 40">
  <path d="M0 40 L0 30 Q60 18 120 30 Q200 14 280 28 Q360 20 440 32 Q520 16 600 30 Q680 22 760 32 Q840 14 920 28 Q1000 20 1080 30 Q1140 18 1200 28 L1200 40 Z" fill="#2a1a10" opacity=".85"/>
</svg>

<footer class="footer abs">
  <nav class="footer-nav abs">
    <a href="#">Home</a><span class="sep">|</span>
    <a href="#">Register</a><span class="sep">|</span>
    <a href="#">Events</a><span class="sep">|</span>
    <a href="#">Get Involved</a><span class="sep">|</span>
    <a href="#">Photos</a><span class="sep">|</span>
    <a href="#">Videos</a><span class="sep">|</span>
    <a href="#">Hall of Fame</a><span class="sep">|</span>
    <a href="#">Who We Are</a><span class="sep">|</span>
    <a href="#">Contact Us</a><span class="sep">|</span>
    <a href="#">T&amp;Cs</a><span class="sep">|</span>
    <a href="#">Privacy</a>
  </nav>
  <div class="copyright abs">Copyright © 2012 Company Name.&nbsp; All Rights Reserved.</div>
</footer>

</body>
</html>
```